Venture Capital Firm Needs Website Redesign

We need a bold revamp of our website (https://halverine.vc/)
which at the moment looks washed out. We want a crisp, fresh and unique look. Feel free to keep as much or as little content in the site. The only thing we need to keep is a team section. The site should convey a clear distinction between our 3 product lines: Venture Capital, Private Credit, and Crypto. Two versions of our logo are attached and they should not change. For design inspirations, we like http://www.9plm.com/ for a more simple site and for a more built out site we like http://bluetorch.com/

Updates
Industry/Entity Type
Investment
Coding
Coded - Design and coding required
Number of Pages Required
1 page
Font styles to use
Colors
Designer to choose colors to be used in the design.
Requirements
Must have
- - Clear distinction between our 3 product lines: Venture Capital, Private Credit
- - Team section

Nice to have
- Some really creative aspect like http://www.9plm.com/ has with the distinction between first, second, and third kind

```html
<!DOCTYPE html>
<html lang="en">
<head>
<meta charset="utf-8">
<title>Halverine</title>
<link rel="stylesheet" href="https://fonts.googleapis.com/css2?family=Lato:wght@400;700&family=Montserrat:wght@500;600&family=Questrial&display=swap">
<style>
:root{
  --green:#8fa63a;
  --green-dark:#7d9330;
  --ink:#2d2d2d;
  --text:#555;
  --light:#efefef;
  --white:#fff;
  --night:#101208;
  --footer:#2f2f2f;
}
*{box-sizing:border-box;margin:0;padding:0}
html,body{width:1200px;height:3051px;overflow:hidden;background:var(--white)}
body{position:relative;font-family:"Lato",sans-serif;color:var(--text)}
.abs{position:absolute}

/* desktop */
.desktop{position:absolute;left:32px;top:36px;width:826px;height:2360px;overflow:hidden;background:var(--light);box-shadow:0 0 6px rgba(0,0,0,.15)}
.desktop .bg{position:absolute;left:0;top:0}
.brand{font-family:"Questrial",sans-serif;letter-spacing:1px;color:var(--white)}
.hero{position:absolute;left:0;top:0;width:826px;height:364px;background:radial-gradient(circle at 68% 50%,#3a4612 0%,#1b200b 40%,#0b0c07 80%)}
.hero .brand{position:absolute;left:68px;top:20px;font-size:26px}
.nav{position:absolute;left:326px;top:26px;display:flex;gap:18px;list-style:none;font-family:"Montserrat",sans-serif;font-size:9.5px;font-weight:600;color:var(--white)}
.hero-glow{position:absolute;left:420px;top:40px;width:300px;height:300px;border-radius:50%;background:radial-gradient(circle,#b4d43c 0%,#5f7a1c 25%,rgba(40,55,10,.6) 55%,rgba(0,0,0,0) 72%)}
.hero h1{position:absolute;left:68px;top:128px;font-family:"Montserrat",sans-serif;font-weight:600;font-size:34px;color:var(--white)}
.hero p{position:absolute;left:68px;top:178px;width:340px;font-size:12.5px;line-height:17px;color:var(--white)}
.btn{position:absolute;height:30px;padding:0 20px;border-radius:15px;font-family:"Montserrat",sans-serif;font-size:10px;font-weight:600;line-height:30px;white-space:nowrap}
.btn-line{border:1.5px solid var(--white);color:var(--white);line-height:27px}
.btn-fill{background:var(--green);color:var(--white)}
.arrow{position:absolute;width:14px;height:22px}

.mark{position:absolute;width:42px;height:42px;border-radius:50%;border:1.5px solid #777}
.mark.on-green{border-color:var(--white)}
.sec-title{position:absolute;font-family:"Montserrat",sans-serif;font-weight:600;font-size:24px;letter-spacing:.5px;color:var(--green)}
.sec-title.white{color:var(--white)}
.rule{position:absolute;width:50px;height:2px;background:var(--green)}
.copy{position:absolute;font-size:11px;line-height:18px;color:var(--text)}
.copy.white{color:var(--white)}
.right{text-align:right}

.logo-box{position:absolute;width:146px;height:62px;background:var(--white);border:1px solid #ddd;display:flex;align-items:center;justify-content:center;font-family:"Lato",sans-serif;font-weight:700;font-size:17px;color:#4a4a4a}
.logo-box.lg{font-size:19px}
.placeholder{position:absolute}

.team-head{position:absolute;left:0;width:826px;text-align:center}
.photo{position:absolute;background:linear-gradient(160deg,#cfcfcf,#8b8b8b);border:2px solid #d8dcc8}
.photo.big{border:3px solid var(--green)}
.member-name{position:absolute;font-family:"Montserrat",sans-serif;font-weight:600;font-size:16px;color:var(--green)}
.member-role{position:absolute;font-size:11px;font-weight:700;color:var(--ink)}
.social{position:absolute;width:24px;height:24px;border-radius:50%;border:1.5px solid var(--green)}

.footer-brand{position:absolute;font-family:"Questrial",sans-serif;color:var(--white);letter-spacing:1px}
.contact-line{position:absolute;font-size:11px;line-height:15px;color:var(--white)}

/* mobile */
.mobile{position:absolute;left:900px;top:108px;width:246px;height:2802px;overflow:hidden;background:var(--white);box-shadow:0 0 6px rgba(0,0,0,.15)}
.m-bar{position:absolute;left:0;top:0;width:246px;height:46px;background:var(--green)}
.m-bar .brand{position:absolute;left:8px;top:11px;font-size:20px}
.burger{position:absolute;right:10px;top:15px;width:18px;height:14px;border-top:3px solid #fff;border-bottom:3px solid #fff}
.burger::after{content:"";position:absolute;left:0;top:2.5px;width:18px;height:3px;background:#fff}
.m-hero{position:absolute;left:0;top:46px;width:246px;height:182px;background:radial-gradient(circle at 78% 45%,#2f4a8a 0%,#14203e 35%,#08090d 75%)}
.m-hero-glow{position:absolute;left:150px;top:20px;width:90px;height:90px;border-radius:50%;background:radial-gradient(circle,#6fa6f2 0%,#2a4f96 40%,rgba(0,0,0,0) 72%)}
.m-hero h2{position:absolute;left:8px;top:58px;font-family:"Montserrat",sans-serif;font-weight:600;font-size:17px;color:#fff}
.m-hero p{position:absolute;left:8px;top:84px;width:130px;font-size:9px;line-height:12px;color:#fff}
.m-sec{position:absolute;left:0;width:246px}
.m-green{background:var(--green)}
.m-mark{position:absolute;left:110px;width:26px;height:26px;border-radius:50%;border:1.2px solid #777}
.m-mark.on-green{border-color:#fff}
.m-title{position:absolute;left:0;width:246px;text-align:center;font-family:"Montserrat",sans-serif;font-weight:600;font-size:17px;color:var(--green)}
.m-title.white{color:#fff}
.m-copy{position:absolute;left:20px;width:206px;text-align:center;font-size:8px;line-height:11.5px;color:var(--text)}
.m-copy.white{color:#fff}
.m-btn{position:absolute;left:100px;width:46px;height:18px;border-radius:9px;font-family:"Montserrat",sans-serif;font-size:6.5px;font-weight:600;line-height:18px;text-align:center}
.m-logo{position:absolute;left:49px;width:148px;height:60px;background:#fff;border:1px solid #ddd;display:flex;align-items:center;justify-content:center;font-weight:700;font-size:16px;color:#4a4a4a}
.m-photo{position:absolute;background:linear-gradient(160deg,#d0d0d0,#8d8d8d)}
.m-social{position:absolute;width:16px;height:16px;border-radius:50%;border:1.2px solid var(--green)}
.m-footer{position:absolute;left:0;top:2602px;width:246px;height:200px;background:var(--footer)}
</style>
</head>
<body>

<!-- Desktop layout -->
<main class="desktop">
  <svg class="bg" width="826" height="2360" viewBox="0 0 826 2360" aria-hidden="true">
    <rect width="826" height="2360" fill="#efefef"/>
    <path d="M0 430 C 220 380 520 350 826 372" fill="none" stroke="#8fa63a" stroke-width="1.5" opacity=".7"/>
    <path d="M0 1072 C 300 1092 600 1090 826 1072 L826 1420 C 560 1400 260 1420 0 1446 Z" fill="#ffffff"/>
    <path d="M0 760 C 250 690 560 690 826 700 L826 1072 C 600 1090 300 1092 0 1072 Z" fill="#8fa63a"/>
    <path d="M0 1446 C 260 1420 560 1396 826 1420 L826 1772 C 600 1792 300 1796 0 1786 Z" fill="#8fa63a"/>
    <path d="M0 2176 C 260 2150 560 2196 826 2148 L826 2360 L0 2360 Z" fill="#2f2f2f"/>
  </svg>

  <header class="hero">
    <div class="hero-glow" role="img" aria-label="Glowing green digital ring artwork"></div>
    <div class="brand">HALVERINE</div>
    <ul class="nav">
      <li>VENTURE</li><li>PRIVATE CREDIT</li><li>CRYPTO</li><li>HALVERINE</li><li>ABOUT US</li><li>TEAM</li><li>BLOG</li>
    </ul>
    <h1>HALVERINE</h1>
    <p>Halverine operates at the intersection of technology and novel asset classes.</p>
    <a class="btn btn-line" style="left:68px;top:238px">Read More</a>
    <svg class="arrow" style="left:28px;top:212px" viewBox="0 0 14 22"><path d="M12 1 L2 11 L12 21 Z" fill="#fff"/></svg>
    <svg class="arrow" style="left:786px;top:212px" viewBox="0 0 14 22"><path d="M2 1 L12 11 L2 21 Z" fill="#fff"/></svg>
  </header>

  <section class="about">
    <div class="mark" style="left:68px;top:410px"></div>
    <h2 class="sec-title" style="left:68px;top:470px">ABOUT US</h2>
    <div class="rule" style="left:68px;top:506px"></div>
    <p class="copy" style="left:68px;top:532px;width:540px">Halverine operates three businesses that bridge technology and finance. We invest in pre-seed venture capital, and build software for the companies we invest in. We manage direct private credit funds that provide private credit capital to alternative private credit platforms, enabling them to finance the loans they originate. We create crypto funds for individuals, IRAs and institutions to get simple and easy access to cryptocurrencies.</p>
    <a class="btn btn-fill" style="left:68px;top:660px">Read More</a>
  </section>

  <section class="venture">
    <div class="mark on-green" style="left:716px;top:756px"></div>
    <div class="logo-box" style="left:68px;top:842px">Tallow Capital</div>
    <div class="logo-box" style="left:230px;top:842px">Pixlane</div>
    <div class="logo-box lg" style="left:68px;top:920px">RoleWeave</div>
    <div class="logo-box lg" style="left:230px;top:920px">Playroute</div>
    <h2 class="sec-title white right" style="left:440px;width:318px;top:842px;font-size:27px">VENTURE CAPITAL</h2>
    <p class="copy white right" style="left:464px;top:884px;width:294px">We invest in early-stage startups led by founders who are passionate and knowledgeable about the markets they serve. We have our own software developers and product managers. We work with the founders in our portfolio to help them bring products to market, earning equity for this work and for the cash we invest in their companies.</p>
    <a class="btn btn-line" style="left:668px;top:1010px">Read More</a>
  </section>

  <section class="credit">
    <div class="mark" style="left:68px;top:1134px"></div>
    <h2 class="sec-title" style="left:68px;top:1194px">PRIVATE CREDIT</h2>
    <div class="rule" style="left:68px;top:1230px"></div>
    <p class="copy" style="left:68px;top:1266px;width:360px">Halverine Private Credit provides capital to lending businesses that are focused on using technology to establish new credit markets, create new credit products or dramatically re-invest an existing form of credit. We believe that the pioneers who build something truly different is a credit market.</p>
    <a class="btn btn-fill" style="left:68px;top:1366px">Read More</a>
    <div class="logo-box" style="left:444px;top:1236px">Corvane</div>
    <div class="logo-box" style="left:606px;top:1236px">Sproutfund</div>
    <div class="logo-box" style="left:526px;top:1316px">Openledge</div>
  </section>

  <section class="crypto">
    <div class="mark on-green" style="left:716px;top:1482px"></div>
    <div class="placeholder" style="left:96px;top:1520px;width:270px;height:236px;background:linear-gradient(180deg,#2a2a2a 0%,#f4f4f4 6%,#e9ecdf 72%,#c8c8c8 100%);border-radius:4px" role="img" aria-label="Desktop monitor showing a crypto index line chart"></div>
    <h2 class="sec-title white right" style="left:520px;width:238px;top:1546px;font-size:27px">CRYPTO</h2>
    <p class="copy white right" style="left:450px;top:1592px;width:308px">The Halverine Crypto Index tracks the top 15 cryptocurrencies weight ed by market cap and rebalanced twice a month. We believe this is the simplest and most cost effective way to obtain cryptocurrency exposure. Our process has been designed by experts from financial services and cryptocurrency industries.</p>
    <a class="btn btn-line" style="left:668px;top:1704px">Read More</a>
  </section>

  <section class="team">
    <h2 class="team-head sec-title" style="top:1838px;font-size:22px">OUR TEAM</h2>
    <p class="team-head" style="top:1874px;font-size:11px;color:var(--ink)">The very best helping the very best.</p>
    <div class="photo" role="img" aria-label="Team member portrait" style="left:68px;top:1936px;width:132px;height:100px"></div>
    <div class="photo" role="img" aria-label="Team member portrait" style="left:202px;top:1936px;width:132px;height:100px"></div>
    <div class="photo" role="img" aria-label="Team member portrait" style="left:68px;top:2040px;width:132px;height:104px"></div>
    <div class="photo" role="img" aria-label="Team member portrait" style="left:202px;top:2040px;width:132px;height:104px"></div>
    <div class="photo big" role="img" aria-label="Featured partner portrait" style="left:340px;top:1936px;width:234px;height:208px"></div>
    <div class="member-name" style="left:590px;top:1966px">OMAR KEDDI</div>
    <div class="member-role" style="left:590px;top:1992px">Partner</div>
    <p class="copy" style="left:590px;top:2014px;width:190px;font-size:10.5px;line-height:16px">Omar is a Partner for Halverine VC Fund. He is also a cofounder of Halverine.</p>
    <div class="social" style="left:590px;top:2064px"></div>
    <div class="social" style="left:622px;top:2064px"></div>
    <svg class="arrow" style="left:26px;top:2030px" viewBox="0 0 14 22"><path d="M12 1 L2 11 L12 21 Z" fill="#333"/></svg>
    <svg class="arrow" style="left:786px;top:2030px" viewBox="0 0 14 22"><path d="M2 1 L12 11 L2 21 Z" fill="#333"/></svg>
  </section>

  <footer class="footer">
    <div class="footer-brand" style="left:68px;top:2282px;font-size:34px">HALVERINE</div>
    <div class="contact-line" style="left:68px;top:2332px;font-size:10px;font-weight:700">Copyrights @ 2018 Halverine. All Rights Reserved.</div>
    <div class="contact-line right" style="left:560px;width:198px;top:2226px;font-family:'Montserrat',sans-serif;font-weight:600;font-size:17px">CONTACT US</div>
    <div class="contact-line right" style="left:560px;width:198px;top:2254px">We would love to hear from you.</div>
    <div class="contact-line right" style="left:540px;width:190px;top:2294px">hello@halverine.vc</div>
    <svg class="abs" style="left:738px;top:2288px" width="22" height="22" viewBox="0 0 22 22"><circle cx="11" cy="11" r="10" fill="none" stroke="#fff" stroke-width="1.3"/><rect x="6" y="7.5" width="10" height="7" fill="none" stroke="#fff" stroke-width="1.2"/><path d="M6 7.5 L11 11.5 L16 7.5" fill="none" stroke="#fff" stroke-width="1.2"/></svg>
    <div class="contact-line right" style="left:540px;width:190px;top:2326px">215 Mercer Row, Suite 404<br>Portland, OR, 97204</div>
    <svg class="abs" style="left:738px;top:2324px" width="22" height="22" viewBox="0 0 22 22"><circle cx="11" cy="11" r="10" fill="none" stroke="#fff" stroke-width="1.3"/><path d="M11 17 C 8 13 7 11 7 9.5 A4 4 0 0 1 15 9.5 C15 11 14 13 11 17 Z" fill="#fff"/><circle cx="11" cy="9.5" r="1.4" fill="#2f2f2f"/></svg>
  </footer>
</main>

<!-- Mobile layout -->
<main class="mobile">
  <div class="m-bar"><div class="brand">HALVERINE</div><div class="burger"></div></div>
  <header class="m-hero">
    <div class="m-hero-glow" role="img" aria-label="Glowing blue digital ring artwork"></div>
    <h2>HALVERINE</h2>
    <p>Halverine operates at the intersection of technology and novel asset classes.</p>
    <div class="m-btn" style="left:8px;top:132px;border:1px solid #fff;color:#fff;line-height:16px">Read More</div>
  </header>

  <section class="m-sec" style="top:228px;height:264px">
    <div class="m-mark" style="top:20px"></div>
    <h3 class="m-title" style="top:60px">ABOUT US</h3>
    <p class="m-copy" style="top:94px">Halverine operates three businesses that bridge technology and finance. We invest in pre-seed venture capital, and build software for the companies we invest in. We manage direct private credit funds that provide private credit capital.</p>
    <div class="m-btn" style="top:208px;background:var(--green);color:#fff">Read More</div>
  </section>

  <section class="m-sec m-green" style="top:492px;height:560px">
    <div class="m-mark on-green" style="top:24px"></div>
    <h3 class="m-title white" style="top:68px">VENTURE CAPITAL</h3>
    <p class="m-copy white" style="top:104px">We invest in early-stage startups led by founders who are passionate and knowledgeable about the markets they serve. We have our own software developers and product managers. We work with the founders in our portfolio to help them bring products to market, earning equity for this work and for the cash we invest in their companies.</p>
    <div class="m-btn" style="top:196px;border:1px solid #fff;color:#fff;line-height:16px">Read More</div>
    <div class="m-logo" style="top:232px;font-size:13px">Tallow Capital</div>
    <div class="m-logo" style="top:302px">Pixlane</div>
    <div class="m-logo" style="top:372px">Playroute</div>
    <div class="m-logo" style="top:442px">RoleWeave</div>
  </section>

  <section class="m-sec" style="top:1052px;height:480px">
    <div class="m-mark" style="top:36px"></div>
    <h3 class="m-title" style="top:80px">PRIVATE CREDIT</h3>
    <p class="m-copy" style="top:112px">Halverine Private Credit provides capital to lending businesses that are focused on using technology to establish new credit markets, create new credit products or dramatically re-invest an existing form of credit. We believe that the pioneers who build something truly different is a credit market.</p>
    <div class="m-btn" style="top:192px;background:var(--green);color:#fff">Read More</div>
    <div class="m-logo" style="top:236px">Corvane</div>
    <div class="m-logo" style="top:312px">Openledge</div>
    <div class="m-logo" style="top:382px">Sproutfund</div>
  </section>

  <section class="m-sec m-green" style="top:1532px;height:420px">
    <div class="m-mark on-green" style="top:28px"></div>
    <h3 class="m-title white" style="top:72px">CRYPTO</h3>
    <p class="m-copy white" style="top:104px">The Halverine Crypto Index tracks the top 15 cryptocurrencies weighted by market cap and rebalanced twice a month. We believe this is the simplest and most cost effective way to obtain cryptocurrency exposure. Our process has been designed by experts from financial services and cryptocurrency industries.</p>
    <div class="m-btn" style="top:188px;border:1px solid #fff;color:#fff;line-height:16px">Read More</div>
    <div class="placeholder" style="left:50px;top:230px;width:146px;height:148px;background:linear-gradient(180deg,#2a2a2a 0%,#f4f4f4 8%,#e9ecdf 72%,#c8c8c8 100%);border-radius:3px" role="img" aria-label="Desktop monitor showing a crypto index line chart"></div>
  </section>

  <section class="m-sec" style="top:1952px;height:650px">
    <h3 class="m-title" style="top:36px">OUR TEAM</h3>
    <p class="m-copy" style="top:64px;color:var(--ink)">The very best helping the very best.</p>
    <div class="m-photo" role="img" aria-label="Team member portrait" style="left:12px;top:102px;width:109px;height:82px"></div>
    <div class="m-photo" role="img" aria-label="Team member portrait" style="left:125px;top:102px;width:109px;height:82px"></div>
    <div class="m-photo" role="img" aria-label="Team member portrait" style="left:12px;top:188px;width:109px;height:82px"></div>
    <div class="m-photo" role="img" aria-label="Team member portrait" style="left:125px;top:188px;width:109px;height:82px"></div>
    <div class="m-photo" role="img" aria-label="Featured partner portrait" style="left:12px;top:298px;width:222px;height:194px"></div>
    <h4 class="m-title" style="top:508px;font-size:15px">OMAR KEDDI</h4>
    <p class="m-copy" style="top:532px;font-weight:700;color:var(--ink)">Partner</p>
    <p class="m-copy" style="top:550px;color:var(--ink)">Omar is a Partner for Halverine VC Fund. He is also a cofounder of Halverine.</p>
    <div class="m-social" style="left:104px;top:596px"></div>
    <div class="m-social" style="left:126px;top:596px"></div>
  </section>

  <footer class="m-footer">
    <div class="footer-brand" style="left:0;width:246px;text-align:center;top:22px;font-size:22px">HALVERINE</div>
    <svg class="abs" style="left:56px;top:74px" width="16" height="16" viewBox="0 0 22 22"><circle cx="11" cy="11" r="10" fill="none" stroke="#fff" stroke-width="1.5"/><rect x="6" y="7.5" width="10" height="7" fill="none" stroke="#fff" stroke-width="1.3"/><path d="M6 7.5 L11 11.5 L16 7.5" fill="none" stroke="#fff" stroke-width="1.3"/></svg>
    <div class="contact-line" style="left:80px;top:76px;font-size:8.5px">hello@halverine.vc</div>
    <svg class="abs" style="left:56px;top:100px" width="16" height="16" viewBox="0 0 22 22"><circle cx="11" cy="11" r="10" fill="none" stroke="#fff" stroke-width="1.5"/><path d="M11 17 C 8 13 7 11 7 9.5 A4 4 0 0 1 15 9.5 C15 11 14 13 11 17 Z" fill="#fff"/></svg>
    <div class="contact-line" style="left:80px;top:98px;font-size:8.5px;line-height:11px">215 Mercer Row, Suite 404<br>Portland, OR, 97204</div>
    <div class="abs" style="left:12px;top:144px;width:222px;height:1px;background:#777"></div>
    <div class="contact-line" style="left:0;width:246px;text-align:center;top:164px;font-size:7.5px;font-weight:700">Copyrights @ 2018 Halverine. All Rights Reserved.</div>
  </footer>
</main>

</body>
</html>
```